Lumen Harbor is a Smart Device and Wiring Business offering the latest in Smart Home Devices inc

Looking for a new website to draw people to my business and explain what a smart home is all about. I currently own a domain and have a website I put together in webquill business website builder. address www.lumenharbor.example. The website needs modernising and be visually appealing with cool action buttons, client feedback page etc.

The webpage needs to present an image of seamless integration of wireless voice control and smart devices that take tasks and activities away from the owner saving them time and money.

I have a facebook business page(lumen harbor) and instagram linked with the business, are we able to link this to the website somehow?

Target Market(s)

Residential home owners who want to modernise their home. Who have seen adverts for corvo hub and pellar mira and want to put it in their home.

Industry/Entity Type

Technology Equipment

Number of Pages Required

1 page

Colors

Designer to choose colors to be used in the design.

Requirements
Must have
• A great landing page, that is modern and attractive, that gets across the idea of smart devices and technology.
• Must be ios/android device friendly.
Nice to have
• interactive/animated buttons
• I like the direction and interactiveness of these websites, a simplified version would be awesome.
• Something in between:
• http://www.quorbeliving.example/ and https://plindo.example/
• http://www.quorbeliving.example/

```html
<!DOCTYPE html>
<html lang="en">
<head>
<meta charset="utf-8">
<title>Lumen Harbor – Smart Device Integration</title>
<link rel="stylesheet" href="https://fonts.googleapis.com/css2?family=Poppins:wght@400;500;600&family=Open+Sans:wght@400;600&display=swap">
<style>
:root{
  --blue:#1f8fd6;
  --navy:#1e3f85;
  --heading:#1e4f93;
  --ink:#222;
  --body:#555;
  --light:#f4f4f4;
  --soft:#f1f1f1;
  --foot:#1d1d1d;
  --white:#fff;
  --star:#f5b91a;
  --ring-bg:#e6e6e6;
}
*{margin:0;padding:0;box-sizing:border-box}
html,body{width:1200px;height:3636px;overflow:hidden}
body{position:relative;font-family:"Open Sans",Arial,sans-serif;color:var(--body);background:var(--white)}
.abs{position:absolute}
h1,h2,h3,h4,.nav,.btn,.logo-name{font-family:"Poppins",Arial,sans-serif}

.site-header{position:absolute;left:0;top:0;width:1200px;height:107px;background:var(--white);border-top:5px solid var(--blue)}
.logo{position:absolute;display:flex;align-items:center;gap:14px}
.logo-dot{width:46px;height:46px;border-radius:50%;background:var(--blue)}
.logo-name{font-size:30px;font-weight:600;color:var(--heading);letter-spacing:.5px}
.site-header .logo{left:87px;top:26px}
.nav{position:absolute;top:46px;font-size:12px;font-weight:500;letter-spacing:.6px;color:#333;text-transform:uppercase}
.nav.active{color:var(--blue)}
.search{position:absolute;left:1062px;top:27px;width:52px;height:52px;border:2px solid var(--blue);border-radius:50%}

.hero{position:absolute;left:0;top:107px;width:1200px;height:511px;
  background:
    radial-gradient(ellipse 180px 260px at 520px 200px,rgba(255,240,200,.75),rgba(255,240,200,0) 70%),
    radial-gradient(ellipse 260px 200px at 1080px 180px,rgba(235,245,250,.9),rgba(235,245,250,0) 75%),
    radial-gradient(ellipse 160px 220px at 470px 300px,rgba(60,120,200,.55),rgba(60,120,200,0) 70%),
    linear-gradient(180deg,rgba(250,246,238,.7) 0%,rgba(250,246,238,0) 30%,rgba(90,70,50,0) 65%,rgba(90,70,50,.45) 100%),
    linear-gradient(90deg,#cfc6b6 0%,#e9e2d4 22%,#a68a66 45%,#7a5d40 55%,#d9cfbe 78%,#eee9e0 100%)}
.cap{position:absolute;left:744px;font-family:"Poppins",sans-serif;color:var(--white);padding:0 18px;display:flex;align-items:center}
.cap-name{top:349px;height:43px;width:262px;background:rgba(20,40,70,.75);font-size:24px}
.cap-tag{top:397px;height:49px;width:366px;background:rgba(31,143,214,.88);font-size:26px}
.dot{position:absolute;top:486px;width:13px;height:13px;border-radius:50%;border:2px solid #ddd;background:#777}

.sec-title{position:absolute;left:0;width:1200px;text-align:center;font-size:32px;font-weight:500;color:var(--heading)}
.sec-sub{position:absolute;left:0;width:1200px;text-align:center;font-size:12px;color:#444}

.services{position:absolute;left:0;top:618px;width:1200px;height:521px;background:var(--light)}
.step{position:absolute;width:260px;text-align:center}
.step svg{display:block;margin:0 auto}
.step h4{font-size:16px;font-weight:600;color:var(--ink);margin-top:26px}
.step p{font-size:12px;line-height:24px;color:#444;margin-top:6px;padding:0 20px}

.feature-photo{position:absolute;width:290px;height:290px;border-radius:50%;border:4px solid #e2e2e2}
.feature h3{position:absolute;font-size:22px;font-weight:600;color:var(--heading)}
.feature p{position:absolute;font-size:12px;line-height:29px;color:#444}
.btn{position:absolute;display:flex;align-items:center;justify-content:center;font-size:14px;font-weight:500;color:var(--white);background:var(--navy)}

.testimonials{position:absolute;left:0;top:2453px;width:1200px;height:495px;background:var(--soft)}
.card{position:absolute;top:141px;width:326px;height:189px;background:var(--white);border:2px solid #e4e4e4;padding:18px 26px}
.quote{font-family:Georgia,serif;font-size:34px;line-height:20px;color:#999;display:inline-block;vertical-align:middle}
.stars{color:var(--star);font-size:15px;letter-spacing:1px;vertical-align:middle}
.card p{font-size:12px;line-height:25px;color:#777;margin-top:14px}
.author{position:absolute;top:352px;display:flex;align-items:center;gap:14px}
.avatar{width:66px;height:66px;border-radius:50%;border:3px solid #fff;background:radial-gradient(circle at 50% 40%,#e2c2a4,#9b7b62 60%,#5e4b3e)}
.author h4{font-size:14px;font-weight:600;color:var(--ink)}
.author span{font-size:12px;color:#777}
.arrow{position:absolute;top:218px}

.about{position:absolute;left:0;top:2948px;width:1200px;height:441px;background:var(--navy);overflow:hidden}
.about h2{position:absolute;left:133px;top:52px;font-size:30px;font-weight:500;color:var(--white)}
.about p{position:absolute;left:133px;width:500px;font-size:12px;line-height:26px;color:#e2e8f5}
.about .btn{background:var(--blue)}

.site-footer{position:absolute;left:0;top:3389px;width:1200px;height:247px;background:var(--foot);color:#ddd}
.site-footer .logo{left:155px;top:78px}
.site-footer .logo-name{color:var(--white)}
.f-head{position:absolute;top:27px;font-family:"Poppins",sans-serif;font-size:15px;font-weight:500;color:var(--white);letter-spacing:.5px}
.f-link{position:absolute;font-size:12px;color:#ddd}
.f-input{position:absolute;left:764px;top:106px;width:290px;height:42px;background:var(--white);font-size:12px;color:#555;padding:13px 14px}
.f-send{position:absolute;left:1054px;top:106px;width:49px;height:42px;background:var(--blue)}
.f-rule{position:absolute;left:155px;top:186px;width:948px;height:1px;background:#3a3a3a}
.copy{position:absolute;left:0;top:210px;width:1200px;text-align:center;font-size:12px;color:#ccc}
</style>
</head>
<body>

<header class="site-header">
  <div class="logo"><span class="logo-dot"></span><span class="logo-name">Lumen Harbor</span></div>
  <span class="nav active" style="left:505px">Home</span>
  <span class="nav" style="left:598px">What We Do</span>
  <span class="nav" style="left:737px">Products</span>
  <span class="nav" style="left:858px">About Us</span>
  <span class="nav" style="left:975px">Contact Us</span>
  <span class="search">
    <svg width="48" height="48" viewBox="0 0 48 48"><circle cx="22" cy="22" r="7" fill="none" stroke="#1f8fd6" stroke-width="3"/><line x1="27" y1="27" x2="32" y2="32" stroke="#1f8fd6" stroke-width="3" stroke-linecap="round"/></svg>
  </span>
</header>

<section class="hero" role="img" aria-label="Hand holding a smartphone with smart home app icons in a bright modern living room">
  <div class="cap cap-name">Lumen Harbor</div>
  <div class="cap cap-tag">Smart Device Integration</div>
  <span class="dot" style="left:572px"></span>
  <span class="dot" style="left:592px;background:#aaa"></span>
  <span class="dot" style="left:611px"></span>
</section>

<section class="services">
  <h2 class="sec-title" style="top:38px">What We Do</h2>
  <p class="sec-sub" style="top:96px">We are a small group of Perth Tech consultants, with long-term experience in the integration, setup and fault finding of advanced</p>

  <div class="step" style="left:59px;top:179px">
    <svg width="170" height="170" viewBox="0 0 170 170">
      <circle cx="85" cy="85" r="64" fill="#e6e6e6"/>
      <circle cx="85" cy="85" r="73" fill="none" stroke="#1f8fd6" stroke-width="5" stroke-dasharray="150 459" transform="rotate(-90 85 85)"/>
      <g fill="#2b8fd0">
        <circle cx="72" cy="70" r="9"/><path d="M56 100 q0-18 16-18 q16 0 16 18z"/>
        <circle cx="99" cy="78" r="7" fill="#5aaee3"/><path d="M86 104 q0-15 13-15 q13 0 13 15z" fill="#5aaee3"/>
      </g>
      <path d="M58 58 a30 30 0 0 1 40 -6" fill="none" stroke="#2b8fd0" stroke-width="3"/>
      <circle cx="158" cy="85" r="14" fill="#1f8fd6" stroke="#fff" stroke-width="3"/><text x="158" y="90" text-anchor="middle" font-size="13" fill="#fff" font-family="Poppins,sans-serif">1</text>
    </svg>
    <h4>Consultation</h4>
    <p>We meet to discuss your vision, gather requirements, and properly scope out timeline and pricing.</p>
  </div>
  <div class="step" style="left:326px;top:179px">
    <svg width="170" height="170" viewBox="0 0 170 170">
      <circle cx="85" cy="85" r="64" fill="#e6e6e6"/>
      <circle cx="85" cy="85" r="73" fill="none" stroke="#1f8fd6" stroke-width="5" stroke-dasharray="230 459" transform="rotate(-90 85 85)"/>
      <g fill="none" stroke="#2b8fd0" stroke-width="3.5" stroke-linecap="round" stroke-linejoin="round">
        <line x1="85" y1="52" x2="85" y2="88"/><polyline points="73,77 85,89 97,77"/>
        <path d="M60 92 v16 h50 v-16"/><line x1="60" y1="116" x2="110" y2="116"/>
      </g>
      <circle cx="85" cy="158" r="14" fill="#1f8fd6" stroke="#fff" stroke-width="3"/><text x="85" y="163" text-anchor="middle" font-size="13" fill="#fff" font-family="Poppins,sans-serif">2</text>
    </svg>
    <h4>Installation</h4>
    <p>Upon acceptance of project document we build your system in our workshop every element for operability.</p>
  </div>
  <div class="step" style="left:604px;top:179px">
    <svg width="170" height="170" viewBox="0 0 170 170">
      <circle cx="85" cy="85" r="64" fill="#e6e6e6"/>
      <circle cx="85" cy="85" r="73" fill="none" stroke="#1f8fd6" stroke-width="5" stroke-dasharray="344 459" transform="rotate(-90 85 85)"/>
      <rect x="64" y="55" width="40" height="54" rx="3" fill="#fff" stroke="#2b8fd0" stroke-width="3"/>
      <g stroke="#2b8fd0" stroke-width="2.5"><line x1="71" y1="67" x2="96" y2="67"/><line x1="71" y1="77" x2="96" y2="77"/><line x1="71" y1="87" x2="86" y2="87"/></g>
      <circle cx="102" cy="103" r="12" fill="#2b8fd0"/>
      <polyline points="96,103 101,108 109,98" fill="none" stroke="#fff" stroke-width="3"/>
      <circle cx="12" cy="85" r="14" fill="#1f8fd6" stroke="#fff" stroke-width="3"/><text x="12" y="90" text-anchor="middle" font-size="13" fill="#fff" font-family="Poppins,sans-serif">3</text>
    </svg>
    <h4>Finalisation</h4>
    <p>After installing the product we run you through your system, making sure you are happy with the</p>
  </div>
  <div class="step" style="left:878px;top:179px">
    <svg width="170" height="170" viewBox="0 0 170 170">
      <circle cx="85" cy="85" r="64" fill="#e6e6e6"/>
      <circle cx="85" cy="85" r="73" fill="none" stroke="#1f8fd6" stroke-width="5"/>
      <path d="M58 90 v-8 a27 27 0 0 1 54 0 v8" fill="none" stroke="#2b8fd0" stroke-width="5"/>
      <rect x="52" y="82" width="14" height="24" rx="5" fill="#2b8fd0"/>
      <rect x="104" y="82" width="14" height="24" rx="5" fill="#2b8fd0"/>
      <path d="M111 106 q0 12 -20 12" fill="none" stroke="#2b8fd0" stroke-width="3"/>
      <circle cx="88" cy="118" r="4" fill="#2b8fd0"/>
      <circle cx="85" cy="12" r="14" fill="#1f8fd6" stroke="#fff" stroke-width="3"/><text x="85" y="17" text-anchor="middle" font-size="13" fill="#fff" font-family="Poppins,sans-serif">4</text>
    </svg>
    <h4>Support</h4>
    <p>We offer tech support when difficulties arise, making sure that your product deliver as advertised.</p>
  </div>
</section>

<h2 class="sec-title" style="top:1180px">Smart Home Specialists</h2>
<p class="sec-sub" style="top:1240px">We are a small group of Perth Tech consultants, with long-term experience in the integration, setup and fault finding of advanced</p>

<article class="feature">
  <div class="feature-photo" role="img" aria-label="Hand holding a phone controlling lights, air conditioner and windows in a living room" style="left:170px;top:1334px;background:radial-gradient(ellipse 50px 80px at 52% 60%,#5d86bd,rgba(93,134,189,0) 100%),linear-gradient(160deg,#eae4da 0%,#cdb99c 40%,#a88765 65%,#dcd2c4 100%)"></div>
  <h3 style="left:521px;top:1340px">Home Automation</h3>
  <p style="left:521px;top:1392px;width:497px">The reality of home automation is that it requires careful planning, impeccable installation, &amp; correct programming in order to reach its full potential. That's exactly what Lumen Harbor will do for you. The first step is finding a solution that fits your lifestyle, it's great to have tech nology in the house, but if it doesn't add value then it's having gadgets for the sake of having gadgets. We at Lumen Harbor want to make your life easier and hassle free.</p>
  <a class="btn" style="left:524px;top:1561px;width:126px;height:46px">Read More</a>
</article>

<article class="feature">
  <h3 style="left:196px;top:1721px">Voice Control With Pellar Mira</h3>
  <p style="left:196px;top:1770px;width:530px">Mira Dot (Pellar Mira) is a hands-free, voice-controlled device with a small built-in speaker—it can also connect to your speakers or headphones over wireless or through a 3.5 mm audio cable to deliver stereo sound to the speakers you choose. Dot connects to the Pellar Mira Voice Service to play music, make calls, send and receive messages, provide information, news, sports scores, weather, and more—instantly.</p>
  <a class="btn" style="left:199px;top:1942px;width:126px;height:46px">Read More</a>
  <div class="feature-photo" role="img" aria-label="Glowing blue smart speaker puck on a dark background" style="left:735px;top:1714px;background:radial-gradient(circle at 50% 42%,#0d1a2c 0,#1a2a40 18%,#57b7ef 22%,#1d6cb5 40%,#0b1c3a 75%)"></div>
</article>

<article class="feature">
  <div class="feature-photo" role="img" aria-label="Hand holding a key fob in front of a glowing blue lock graphic" style="left:170px;top:2095px;background:radial-gradient(circle at 40% 50%,#e9f7ff,#6cc3f2 30%,#1e7fc4 60%,#9bb8cf 100%)"></div>
  <h3 style="left:521px;top:2104px">Keyless Entry</h3>
  <p style="left:521px;top:2156px;width:497px">The days of locking your keys in the house or forgetting to lock the door can be a thing of the past, thanks to the variety of affordable electronic door locks on the market. Once the domain of the wealthy for entry to their multi million dollar estates, an electronic door lock can now grace your front door Before we explore the features on some popular electronic locks, let's learn more about how they work.</p>
  <a class="btn" style="left:524px;top:2325px;width:126px;height:46px">Read More</a>
</article>

<section class="testimonials">
  <h2 class="sec-title" style="top:24px">Client Testimonials</h2>
  <p class="sec-sub" style="top:86px">We are a small group of Perth Tech consultants, with long-term experience in the integration, setup and fault finding of advanced</p>

  <svg class="arrow" style="left:36px" width="24" height="74" viewBox="0 0 24 74"><polyline points="20,2 4,37 20,72" fill="none" stroke="#c8c8c8" stroke-width="2"/></svg>
  <svg class="arrow" style="left:1142px" width="24" height="74" viewBox="0 0 24 74"><polyline points="4,2 20,37 4,72" fill="none" stroke="#c8c8c8" stroke-width="2"/></svg>

  <div class="card" style="left:87px"><span class="quote">&ldquo;</span> <span class="stars">★★★★★</span><p>Sed ut perspiciatis unde omnis iste natus error sit voluptatem accusantium doloremque laudantium, totam rem aperiam, eaque ipsa quae ab illo inven tore veritatis et quasi architecto beatae vitae dicta sunt explicabo.</p></div>
  <div class="card" style="left:437px"><span class="quote">&ldquo;</span> <span class="stars">★★★★★</span><p>Sed ut perspiciatis unde omnis iste natus error sit voluptatem accusantium doloremque laudantium, totam rem aperiam, eaque ipsa quae ab illo inven tore veritatis et quasi architecto beatae vitae dicta sunt explicabo.</p></div>
  <div class="card" style="left:787px"><span class="quote">&ldquo;</span> <span class="stars">★★★★★</span><p>Sed ut perspiciatis unde omnis iste natus error sit voluptatem accusantium doloremque laudantium, totam rem aperiam, eaque ipsa quae ab illo inven tore veritatis et quasi architecto beatae vitae dicta sunt explicabo.</p></div>

  <div class="author" style="left:98px"><span class="avatar" role="img" aria-label="Client portrait"></span><div><h4>RAVI TOLLAND</h4><span>Posted on 28 Apr 2018</span></div></div>
  <div class="author" style="left:448px"><span class="avatar" role="img" aria-label="Client portrait"></span><div><h4>RAVI TOLLAND</h4><span>Posted on 28 Apr 2018</span></div></div>
  <div class="author" style="left:798px"><span class="avatar" role="img" aria-label="Client portrait"></span><div><h4>RAVI TOLLAND</h4><span>Posted on 28 Apr 2018</span></div></div>
</section>

<section class="about">
  <h2>About Lumen Harbor</h2>
  <p style="top:118px">Our aim is to bring affordable smart home products to everyone, offering seamless inte gration and reliability. With a wide range of available cost options, outstanding service &amp; experience, we are the solution for all your smart home technology solutions. We are a passionate group of tech specialists who have years of experience with installing, using and troubleshooting residential and industrial technology systems.</p>
  <p style="top:266px">Lumen Harbor began as an idea in a garage and a belief that home technology should be readily available and reasonably priced.</p>
  <a class="btn" style="left:136px;top:339px;width:126px;height:41px">Read More</a>
  <svg class="abs" style="left:712px;top:-50px" width="520" height="520" viewBox="0 0 520 520">
    <circle cx="258" cy="253" r="250" fill="#1f8fd6"/>
    <path d="M30 330 A250 250 0 0 0 460 400" fill="none" stroke="#111" stroke-width="16"/>
    <circle cx="262" cy="250" r="232" fill="#f3f3f3"/>
  </svg>
  <div class="abs" role="img" aria-label="Smiling couple looking at a tablet together on a sofa" style="left:752px;top:-22px;width:444px;height:444px;border-radius:50%;background:radial-gradient(ellipse 90px 70px at 32% 68%,#dfe4ea,rgba(223,228,234,0) 100%),linear-gradient(120deg,#f1ede8 0%,#d7b596 25%,#a97b58 48%,#5b4436 62%,#c89c7a 80%,#ece7e1 100%)"></div>
</section>

<footer class="site-footer">
  <div class="logo"><span class="logo-dot"></span><span class="logo-name">Lumen Harbor</span></div>
  <h4 class="f-head" style="left:482px">QUICK LINKS</h4>
  <a class="f-link" style="left:482px;top:70px">Home</a>
  <a class="f-link" style="left:482px;top:99px">What We Do</a>
  <a class="f-link" style="left:482px;top:128px">Products</a>
  <a class="f-link" style="left:604px;top:70px">About Us</a>
  <a class="f-link" style="left:604px;top:99px">Contact Us</a>
  <h4 class="f-head" style="left:764px">NEWSLETTER</h4>
  <p class="f-link" style="left:764px;top:68px">Sed ut perspiciatis unde omnis iste natus error sit</p>
  <div class="f-input">Enter Your Email Id</div>
  <div class="f-send"><svg width="49" height="42" viewBox="0 0 49 42"><polygon points="16,21 33,13 28,30 24,23" fill="#fff"/></svg></div>
  <div class="f-rule"></div>
  <p class="copy">© Copy Right -2018 Lumen Harbor All rights reserved.</p>
</footer>

</body>
</html>
```